Modern Verdell Tree Care Website

I need a website for a full service Tree Care company. The company provides tree pruning, tree removal, tree preservation, emergency services, stump grinding, and emergency tree services.

Target Market(s)

Customers that need tree services

Industry/Entity Type

Landscaping, Tree Services

Coding

Coded - Design and coding required

Number of Pages Required

5+ page

Font styles to use
Sans Serif

Requirements
Must have
• Good clean design that showcases the services the company provides.
Nice to have
• Services page; contact form, blog, home page, about page

```html
<!DOCTYPE html>
<html lang="en">
<head>
<meta charset="utf-8">
<title>Verdell Tree Care – Services</title>
<link href="https://fonts.googleapis.com/css2?family=Montserrat:wght@400;500;600;700&family=Kumbh+Sans:wght@400;500;600;700&display=swap" rel="stylesheet">
<style>
:root{
  --green:#7dbb3c;
  --green-dark:#4e7a1d;
  --orange:#f8a928;
  --orange-light:#fbbf45;
  --slate:#3a464c;
  --text:#33383b;
  --footer-bg:#fbfafa;
  --copy-bg:#f2f1ec;
  --rule:#d6d6d6;
}
*{margin:0;padding:0;box-sizing:border-box}
html,body{width:925px;height:1200px;overflow:hidden;background:#fff}
body{position:relative;font-family:"Kumbh Sans",sans-serif;color:var(--text)}
.abs{position:absolute}
/* header */
.site-header{position:absolute;left:0;top:0;width:925px;height:62px;background:#fff}
.brand{position:absolute;display:flex;align-items:center;gap:6px;font-family:"Montserrat",sans-serif;font-weight:700;color:var(--slate);white-space:nowrap}
.brand .mark{display:block;background:var(--green)}
.header-brand{left:74px;top:18px;font-size:17px}
.header-brand .mark{width:20px;height:20px}
.main-nav a{position:absolute;top:26px;font-family:"Montserrat",sans-serif;font-size:10.5px;font-weight:500;color:var(--slate);text-decoration:none;transform:translateX(-50%)}
.main-nav a.active{color:var(--green)}
.main-nav a.active::after{content:"";position:absolute;left:12px;right:12px;top:18px;height:1.5px;background:var(--slate)}
.call-btn{position:absolute;left:728px;top:12px;width:135px;height:36px;border-radius:18px;background:var(--green);color:#fff;font-size:11px;font-weight:600;display:flex;align-items:center;padding-left:14px;gap:6px}
.call-btn .ico{width:20px;height:20px;border-radius:50%;background:#fff;display:flex;align-items:center;justify-content:center}
/* hero */
.hero{position:absolute;left:0;top:62px;width:925px;height:292px;overflow:hidden}
.hero-photo{position:absolute;inset:0;background:linear-gradient(100deg,#5b5a4b 0%,#6f8a44 35%,#a7c84f 60%,#c6d98a 75%,#7fa04a 100%)}
.hero-eyebrow{position:absolute;left:91px;top:101px;color:#fff;font-family:"Montserrat",sans-serif;font-size:13px;font-weight:500;letter-spacing:.3px}
.hero-title{position:absolute;left:88px;top:120px;color:#fff;font-family:"Montserrat",sans-serif;font-size:30px;font-weight:700}
/* service */
.service-title{position:absolute;left:92px;top:448px;font-family:"Montserrat",sans-serif;font-size:27px;font-weight:400;color:var(--green)}
.service-title strong{font-weight:700;color:var(--slate)}
.title-rule{position:absolute;left:93px;top:485px;width:52px;height:2px;background:linear-gradient(90deg,var(--green) 50%,var(--orange) 50%)}
.title-mark{position:absolute;left:93px;top:424px;width:22px;height:22px;background:var(--green)}
.service-copy{position:absolute;left:91px;top:503px;width:392px;font-size:12.4px;line-height:17.85px}
.service-copy p+p{margin-top:18px}
/* footer */
.site-footer{position:absolute;left:0;top:955px;width:925px;height:245px;background:var(--footer-bg);border-top:1px solid var(--rule)}
.footer-brand{left:50%;transform:translateX(-50%);top:40px;font-size:22px}
.footer-brand .mark{width:26px;height:26px}
.footer-rule{position:absolute;left:56px;width:767px;height:1px;background:var(--rule)}
.footer-nav{position:absolute;left:0;top:103px;width:925px;font-family:"Montserrat",sans-serif;font-size:11px;font-weight:600;color:var(--text)}
.footer-nav span{position:absolute;transform:translateX(-50%)}
.footer-nav i{position:absolute;width:3px;height:3px;background:var(--green);top:6px}
.contact-item{position:absolute;top:158px;display:flex;align-items:center;gap:5px;font-size:11px;font-weight:700}
.contact-item .ico{width:27px;height:27px;border-radius:50%;background:var(--green);display:flex;align-items:center;justify-content:center}
.social{position:absolute;top:163px;width:20px;height:20px;border-radius:50%}
.copyright{position:absolute;left:0;top:205px;width:925px;height:40px;background:var(--copy-bg);text-align:center;line-height:40px;font-size:11px;color:#444}
</style>
</head>
<body>
<header class="site-header">
  <div class="brand header-brand"><span class="mark"></span>Verdell Tree Care</div>
  <nav class="main-nav">
    <a style="left:288px">HOME</a>
    <a style="left:363px">ABOUT US</a>
    <a class="active" style="left:449px">SERVICES</a>
    <a style="left:522px">BLOG</a>
    <a style="left:590px">REVIEW</a>
    <a style="left:679px">CONTACT US</a>
  </nav>
  <div class="call-btn"><span class="ico"><svg width="11" height="11" viewBox="0 0 24 24"><path fill="#7dbb3c" d="M6.6 10.8a15.1 15.1 0 0 0 6.6 6.6l2.2-2.2a1 1 0 0 1 1-.25 11.4 11.4 0 0 0 3.6.57 1 1 0 0 1 1 1V20a1 1 0 0 1-1 1A17 17 0 0 1 3 4a1 1 0 0 1 1-1h3.5a1 1 0 0 1 1 1c0 1.25.2 2.45.57 3.6a1 1 0 0 1-.25 1z"/></svg></span>(555) 214 7730</div>
</header>

<section class="hero">
  <div class="hero-photo" role="img" aria-label="Two arborists in high-visibility shirts and helmets cutting a fallen tree branch on a lawn"></div>
  <svg class="abs" style="left:0;top:0" width="925" height="292">
    <polygon points="0,0 452,0 292,292 0,292" fill="#7dbb3c" opacity=".97"/>
  </svg>
  <div class="hero-eyebrow">WHAT WE DO</div>
  <h1 class="hero-title">OUR SERVICES</h1>
</section>

<section class="service">
  <svg class="abs" style="left:560px;top:398px" width="365" height="476">
    <defs><linearGradient id="orangeFill" x1="0" y1="0" x2="1" y2="1"><stop offset="0" stop-color="#fbbf45"/><stop offset="1" stop-color="#f6a321"/></linearGradient></defs>
    <polygon points="237,0 365,0 365,476 11,476" fill="url(#orangeFill)" role="img" aria-label="Warm orange-tinted photo of a tree trunk"/>
  </svg>
  <svg class="abs" style="left:495px;top:435px" width="380" height="380">
    <defs><linearGradient id="pruneFill" x1="0" y1="0" x2="1" y2="1"><stop offset="0" stop-color="#6a5a45"/><stop offset=".5" stop-color="#8a7a62"/><stop offset="1" stop-color="#c26a2c"/></linearGradient></defs>
    <circle cx="189" cy="188" r="181" fill="#4e7a1d"/>
    <circle cx="196" cy="188" r="174" fill="#f8a928"/>
    <circle cx="196" cy="188" r="168" fill="url(#pruneFill)" role="img" aria-label="Gloved hand pruning a branch with a folding hand saw"/>
  </svg>
  <span class="title-mark"></span>
  <h2 class="service-title"><strong>TREE</strong> PRUNING</h2>
  <span class="title-rule"></span>
  <div class="service-copy">
    <p>Lorem ipsum dolor sit amet, consectetur adipiscing elit, sed do eiusmod tempor incididunt ut labore et dolore magna aliqua. Ut enim ad minim veniam, quis nostrud exercitation ullamco laboris nisi ut aliquip ex ea commodo consequat. Duis aute irure dolor in reprehenderit in voluptate velit esse cillum dolore eu fugiat nulla pariatur. Excepteur sint occaecat cupidatat non proident, sunt in culpa qui officia deserunt mollit anim id est laborum.</p>
    <p>Sed ut perspiciatis unde omnis iste natus error sit voluptatem accusantium doloremque laudantium, totam rem aperiam, eaque ipsa quae ab illo inventore veritatis et quasi architecto beatae vitae dicta sunt explicabo. vatem quia voluptas sit aspernatur aut odit aut fugit, sed quia consequuntur magni dolores eos qui ratione voluptatem sequi nesciunt. Neque porro quisquam est, qui dolorem ipsum quia dolor sit amet, consectetur, adipisci velit, sednventore veritatis et quasi architecto beatae vitae dicta sunt explicabo. vatem quia voluptas sit aspernatur aut odit aut fugit, sed quia consequuntur magni dolores eos qui</p>
  </div>
</section>

<footer class="site-footer">
  <div class="brand footer-brand abs"><span class="mark"></span>Verdell Tree Care</div>
  <div class="footer-rule" style="top:83px"></div>
  <nav class="footer-nav">
    <span style="left:152px">HOME</span><i style="left:202px"></i>
    <span style="left:261px">ABOUT US</span><i style="left:321px"></i>
    <span style="left:380px">SERVICES</span><i style="left:435px"></i>
    <span style="left:490px">BLOGS</span><i style="left:536px"></i>
    <span style="left:598px">REVIEWS</span><i style="left:655px"></i>
    <span style="left:711px">CONTACT</span>
  </nav>
  <div class="footer-rule" style="top:137px"></div>
  <div class="contact-item" style="left:128px"><span class="ico"><svg width="13" height="13" viewBox="0 0 24 24"><path fill="#fff" d="M6.6 10.8a15.1 15.1 0 0 0 6.6 6.6l2.2-2.2a1 1 0 0 1 1-.25 11.4 11.4 0 0 0 3.6.57 1 1 0 0 1 1 1V20a1 1 0 0 1-1 1A17 17 0 0 1 3 4a1 1 0 0 1 1-1h3.5a1 1 0 0 1 1 1c0 1.25.2 2.45.57 3.6a1 1 0 0 1-.25 1z"/></svg></span>(555) 214-7730</div>
  <div class="contact-item" style="left:309px"><span class="ico"><svg width="13" height="13" viewBox="0 0 24 24"><path fill="#fff" d="M6.6 10.8a15.1 15.1 0 0 0 6.6 6.6l2.2-2.2a1 1 0 0 1 1-.25 11.4 11.4 0 0 0 3.6.57 1 1 0 0 1 1 1V20a1 1 0 0 1-1 1A17 17 0 0 1 3 4a1 1 0 0 1 1-1h3.5a1 1 0 0 1 1 1c0 1.25.2 2.45.57 3.6a1 1 0 0 1-.25 1z"/></svg></span>(555) 380-4162</div>
  <div class="contact-item" style="left:464px;gap:7px"><span class="ico"><svg width="13" height="10" viewBox="0 0 26 20"><rect x="1" y="1" width="24" height="18" rx="2" fill="#fff"/><path d="M2 3l11 8 11-8" fill="none" stroke="#7dbb3c" stroke-width="2"/></svg></span>hello@verdelltreecare.com</div>
  <span class="social" style="left:691px;background:var(--slate)" aria-label="Social link"></span>
  <span class="social" style="left:720px;background:var(--green)" aria-label="Social link"></span>
  <span class="social" style="left:750px;background:var(--green)" aria-label="Social link"></span>
  <span class="social" style="left:781px;background:var(--green)" aria-label="Social link"></span>
  <div class="copyright">Copyright © 2024 Verdell Tree Care | &nbsp;All Right Reserved</div>
</footer>
</body>
</html>
```